" A Vardim Soluçoes Ambientais é uma empresa que presta serviços de regularizaçao ambiental. Trata-se de uma consultoria ambiental cujo principal serviço é oferecer soluçoes ambientais para atividades produtivas e imóveis urbanos ou rurais. Exemplos: (i) correçao de matrículas e registros em órgao públicos para fazendas produtivas; (ii) correçao de emissoes atmosféricas, ruídos, resíduos, etc, de indústrias; (iii) descontaminaçao do solo ou água subterrânea de um imóvel; (iv) elaboraçao de laudos técnicos sobre passivos ambientais. Observaçao importante: a empresa nao é uma ONG, embora o apelo seja ambiental. "

```html
<!DOCTYPE html>
<html lang="pt-BR">
<head>
<meta charset="utf-8">
<title>Vardim Soluçoes Ambientais – Papel timbrado</title>
<link rel="stylesheet" href="https://fonts.googleapis.com/css2?family=Questrial&display=swap">
<style>
  :root {
    --backdrop: #e7e8e6;
    --paper: #ffffff;
    --brand-green: #24473a;
    --rule-grey: #8a948f;
    --text-grey: #5b605d;
    --tagline-grey: #8d918f;
  }
  * { margin: 0; padding: 0; box-sizing: border-box; }
  html, body {
    width: 1200px;
    height: 1200px;
    overflow: hidden;
    background: var(--backdrop);
  }
  .canvas {
    position: relative;
    width: 1200px;
    height: 1200px;
  }
  .letterhead {
    position: absolute;
    left: 218px;
    top: 60px;
    width: 764px;
    height: 1080px;
    background: var(--paper);
    box-shadow: 0 2px 10px rgba(0, 0, 0, 0.12);
    font-family: "Questrial", sans-serif;
  }
  .brand {
    position: absolute;
    top: 52px;
    left: 0;
    right: 0;
    text-align: center;
  }
  .brand-row {
    display: inline-flex;
    align-items: center;
    gap: 10px;
  }
  .brand-name {
    font-size: 54px;
    line-height: 1;
    letter-spacing: 2px;
    color: var(--brand-green);
  }
  .brand-dot {
    width: 14px;
    height: 14px;
    border-radius: 50%;
    background: var(--brand-green);
  }
  .brand-tagline {
    margin-top: 4px;
    font-size: 9px;
    letter-spacing: 4.2px;
    text-transform: uppercase;
    color: var(--tagline-grey);
  }
  .contact {
    position: absolute;
    left: 14px;
    bottom: 40px;
    font-size: 11.5px;
    line-height: 16px;
    color: var(--text-grey);
    list-style: none;
  }
  .footer-rule {
    position: absolute;
    left: 0;
    right: 0;
    bottom: 10px;
    height: 12px;
  }
  .footer-rule svg { display: block; width: 100%; height: 100%; }
</style>
</head>
<body>
<main class="canvas">
  <article class="letterhead">
    <header class="brand">
      <div class="brand-row">
        <span class="brand-name">VARDIM</span>
        <span class="brand-dot"></span>
      </div>
      <p class="brand-tagline">soluçoes ambientais</p>
    </header>

    <ul class="contact">
      <li>rua das palmeiras 240 2º andar jardim sul</li>
      <li>04512 000 são paulo sp brasil</li>
      <li>+55 11 4000 1234</li>
      <li>www.vardimsolucoesambientais.com.br</li>
    </ul>

    <div class="footer-rule">
      <svg viewBox="0 0 764 12" preserveAspectRatio="none" aria-hidden="true">
        <rect x="0" y="0" width="764" height="4" fill="var(--rule-grey)"/>
        <rect x="0" y="4" width="764" height="8" fill="var(--brand-green)"/>
      </svg>
    </div>
  </article>
</main>
</body>
</html>
```